Podiatry clinic requires a modern revamp and editing of existing website.

I would like a fresh new look and updated information for my current business website. An easy to navigate site with prominent address and phone number for call to action. We are a podiatry clinic that focuses on general and sports podiatry.
I would like 4 pages; including Home page, About Us, Services & Contact.
www.brambleridgepodiatry.net

Target Market(s)

Active working professionals.

Industry/Entity Type

Medical

Coding

Coded - Design and coding required

Number of Pages Required

4 page

Font styles to use
Sans Serif

Colors
6b449b

Requirements
Must have
• A modern look with logo and active images; clean and uncluttered. Visible phone number and address for call to action.
• 4 pages - Home, About Us, Services, Contact.
• Home page - update address & service logos.
• About Us - update of personal information.
• Services - Revamp of existing page.
• Contact page to include Google map, email & phone number.
Nice to have
• Ability to add content easily; eg. a blog or adding video onto Home page.
• Link to plain circle link page.

```html
<!DOCTYPE html>
<html lang="en">
<head>
<meta charset="utf-8">
<title>Bramble Ridge Podiatry — Services</title>
<link href="https://fonts.googleapis.com/css2?family=Open+Sans:wght@400;600&family=Raleway:wght@300;400&family=Roboto+Condensed:wght@300;400&display=swap" rel="stylesheet">
<style>
:root{
  --purple:#6b449b;
  --green:#7dbb2c;
  --text:#555;
  --muted:#777;
  --line:#6b449b;
  --grey-bg:#ececec;
  --white:#fff;
  --photo-dark:#3a3538;
  --photo-warm:#6e5a50;
  --skin:#e2bfa9;
  --map:#e4e0d8;
}
*{box-sizing:border-box;margin:0;padding:0}
html,body{width:1200px;height:4265px;overflow:hidden}
body{font-family:"Open Sans",sans-serif;color:var(--text);background:var(--white);position:relative}
a{text-decoration:none}

/* Hero */
.hero{position:relative;height:677px;overflow:hidden}
.photo-fill{position:absolute;inset:0;background:linear-gradient(180deg,var(--photo-warm) 0%,var(--photo-dark) 100%)}
.brand{position:absolute;left:80px;top:20px;display:flex;align-items:center;gap:14px}
.brand-mark{width:54px;height:54px;border-radius:50%;background:var(--purple)}
.brand-name{font-weight:600;font-size:24px;color:var(--white);line-height:1.15;width:190px}
.top-contact{position:absolute;right:90px;top:42px;text-align:right;color:var(--white);font-size:19px}
.top-contact p{display:flex;align-items:center;justify-content:flex-end;gap:10px;margin-bottom:30px}
.top-contact strong{font-weight:600}
.hero-copy{position:absolute;left:0;right:0;top:250px;text-align:center;color:var(--white)}
.hero-title{font-family:"Roboto Condensed",sans-serif;font-weight:400;font-size:78px;letter-spacing:1px}
.hero-sub{font-family:"Roboto Condensed",sans-serif;font-weight:300;font-size:40px;margin-top:34px}
.btn{display:inline-block;background:var(--purple);color:var(--white);font-size:17px;text-transform:uppercase;padding:14px 26px}
.hero .btn{margin-top:28px}

/* Nav */
.main-nav{height:63px;background:var(--purple);display:flex;padding-left:77px}
.main-nav a{display:flex;align-items:center;justify-content:center;width:123px;color:var(--white);font-size:18px;text-transform:uppercase}
.main-nav a.active{background:var(--green)}

/* Services */
.services{position:relative;height:1717px;padding-top:58px}
.deco-foot{position:absolute;left:0;top:0;width:200px;height:255px;background:var(--skin)}
.section-title{font-family:"Raleway",sans-serif;font-weight:300;font-size:50px;text-align:center;color:#444;text-transform:uppercase}
.section-title span{color:var(--purple)}
.intro{width:720px;margin:14px auto 0;text-align:center;font-size:15px;line-height:1.55;color:var(--muted)}
.sub-title{font-family:"Raleway",sans-serif;font-weight:300;font-size:38px;text-align:center;color:#444;margin-top:30px}
.sub-title span{color:var(--purple);font-weight:400}
.treatments{list-style:none;margin:24px 77px 0}
.treatment{display:flex;height:180px;padding-top:10px}
.thumb{flex:0 0 132px;height:132px;border-radius:50%;border:2px solid #c9b8dd;background:var(--skin);margin-right:20px}
.treatment-body{flex:1;border-bottom:2px solid var(--line);padding-top:10px;height:165px}
.treatment:last-child .treatment-body{border-bottom:none}
.treatment h3{font-weight:400;font-size:22px;color:var(--purple);margin-bottom:10px}
.treatment p{font-size:15px;line-height:1.6;color:var(--muted)}

/* Specialised */
.specialised{position:relative;height:1018px;background:var(--grey-bg);padding-top:48px}
.deco-feet{position:absolute;right:0;top:-20px;width:290px;height:170px;background:var(--skin)}
.specialised .sub-title{margin-top:0;position:relative}

/* Partners */
.partners{height:180px;display:flex;align-items:center;justify-content:space-between;padding:0 80px}
.badge{height:80px;border-radius:6px}
.badge-a{width:210px;background:#2a4d9c}
.badge-b{width:220px;background:#1d4fa0}
.badge-c{width:220px;background:#3aa34a}
.badge-d{width:240px;background:#2a2a2a}

/* Contact */
.contact{position:relative;height:555px;color:var(--white);overflow:hidden}
.contact .photo-fill{background:linear-gradient(180deg,#6f6657 0%,#33362c 100%)}
.contact .section-title{position:relative;color:var(--white);padding-top:45px;font-size:46px}
.contact-form{position:absolute;left:77px;top:162px;width:438px}
.field{display:block;width:100%;height:52px;background:var(--white);border:none;margin-bottom:6px;padding:0 16px;font-family:"Open Sans",sans-serif;font-size:15px;color:#999}
.field-message{height:104px;padding-top:12px;resize:none}
.submit{margin-top:12px;width:166px;height:52px;border:none;border-radius:26px;background:var(--purple);color:var(--white);font-family:"Open Sans",sans-serif;font-size:20px;text-transform:uppercase}
.map{position:absolute;left:535px;top:162px;width:275px;height:273px;background:var(--map)}
.contact-address{position:absolute;left:853px;top:165px;width:300px;font-size:16px;line-height:1.5}
.contact-address h4{font-family:"Raleway",sans-serif;font-weight:400;font-size:22px;text-transform:uppercase;margin-bottom:22px}
.contact-address p{display:flex;gap:12px;margin-bottom:16px;align-items:flex-start}
.contact-address svg{flex:0 0 auto;margin-top:3px}
.social{display:block;width:48px;height:48px;border-radius:50%;background:var(--white);margin-left:34px}

.site-footer{height:55px;background:var(--purple);color:var(--white);text-align:center;font-size:15px;line-height:55px}
</style>
</head>
<body>

<header class="hero">
  <div class="photo-fill" role="img" aria-label="Photo: runner's feet on an open road at sunset"></div>
  <a class="brand" href="#"><span class="brand-mark"></span><span class="brand-name">Bramble Ridge Podiatry</span></a>
  <div class="top-contact">
    <p><svg width="18" height="24" viewBox="0 0 18 24"><path d="M9 0C4 0 0 4 0 9c0 7 9 15 9 15s9-8 9-15c0-5-4-9-9-9zm0 12a3 3 0 110-6 3 3 0 010 6z" fill="#fff"/></svg>Suite 12 / 88 Harrow Lane Ashvale 3100</p>
    <p><svg width="24" height="24" viewBox="0 0 24 24"><path d="M6.6 10.8a15 15 0 006.6 6.6l2.2-2.2c.3-.3.7-.4 1-.2 1.1.4 2.3.6 3.6.6.6 0 1 .4 1 1V20c0 .6-.4 1-1 1A17 17 0 013 4c0-.6.4-1 1-1h3.5c.6 0 1 .4 1 1 0 1.3.2 2.5.6 3.6.1.3 0 .7-.2 1z" fill="#fff"/></svg>CALL US NOW : <strong>1300 555 274</strong></p>
  </div>
  <div class="hero-copy">
    <h1 class="hero-title">Don't let pain run your life</h1>
    <p class="hero-sub">Choose to be pain free</p>
    <a class="btn" href="#">Book an appointment</a>
  </div>
</header>

<nav class="main-nav">
  <a class="active" href="#">Home</a>
  <a href="#">About</a>
  <a href="#">Services</a>
  <a href="#">Contact</a>
</nav>

<section class="services">
  <div class="deco-foot" role="img" aria-label="Photo: hand holding a sore heel"></div>
  <h2 class="section-title">Services <span>we provide</span></h2>
  <p class="intro">Podiatrists are trained to diagnose and treat all medical conditions that affect the feet and lower limb. At Bramble Ridge Podiatry we provide treatment for general &amp; Sports Podiatry conditions and various specialised treatments:</p>
  <h3 class="sub-title">General <span>Treatments</span></h3>
  <ul class="treatments">
    <li class="treatment"><div class="thumb" role="img" aria-label="Photo: nail care"></div><div class="treatment-body"><h3>Nails</h3><p>Nails for difficult to reach feet; ingrown nails; overly thick nails; fungal nails; nails subjected to trauma.</p></div></li>
    <li class="treatment"><div class="thumb" role="img" aria-label="Photo: corn on a foot"></div><div class="treatment-body"><h3>Corns</h3><p>Corns - hard dry skin lesions due to concentrated pressure from footwear or abnormal foot structure.</p></div></li>
    <li class="treatment"><div class="thumb" role="img" aria-label="Photo: callus treatment"></div><div class="treatment-body"><h3>Callus</h3><p>Callus - areas of dry skin due to pressure of friction, especially around the heels or bony parts of the feet.</p></div></li>
    <li class="treatment"><div class="thumb" role="img" aria-label="Photo: wart on a foot"></div><div class="treatment-body"><h3>Warts</h3><p>Warts - also called Papillomas or Verrucare are a viral infection that causes a lesion on the feet. Warts are commonly contracted from public swimming pools and wet tiled surfaces.</p></div></li>
    <li class="treatment"><div class="thumb" role="img" aria-label="Photo: skin condition on a foot"></div><div class="treatment-body"><h3>Skin Disorders</h3><p>Skin Disorders - fungal infections/ tinea/athlete's foot; dermatitis, sweating feet; foot odour; dry cracked skin.</p></div></li>
    <li class="treatment"><div class="thumb" role="img" aria-label="Photo: heel pain"></div><div class="treatment-body"><h3>Heel pain / Heel Spurs / &nbsp;Arch pain</h3><p>Heel pain / Heel Spurs / &nbsp;Arch pain - Plantar Fasciitis - Common condition that causes pain around the heel or arch area that is caused by factors such as faulty foot biomechanics, poor footwear, sports or work activities, injuries and obesity.</p></div></li>
    <li class="treatment"><div class="thumb" role="img" aria-label="Photo: ankle and shin pain"></div><div class="treatment-body"><h3>Ankle pain / Shin splints / Knee pain</h3><p>Ankle pain / Shin splints / Knee pain - faulty foot biomechanics or injuries can cause excessive strain and damage to soft tissues like muscles &amp; tendons or bones &amp; joints./ These can be treated with various physical therapies and orthoses/arch supports.</p></div></li>
    <li class="treatment"><div class="thumb" role="img" aria-label="Photo: bunion on a foot"></div><div class="treatment-body"><h3>Bunions / Hammertoes / Toe deformities</h3><p>Bunions / Hammertoes / Toe deformities - Bony joint deformities can be caused by faluty foot biomechanics and conditions such as Arthritis, Diabetes or Gout. We can help manage pain and prevent these conditions from getting worse with various products that supply padding or support, as well as provide advice on appropriate footwear.</p></div></li>
  </ul>
</section>

<section class="specialised">
  <div class="deco-feet" role="img" aria-label="Photo: bare feet resting"></div>
  <h3 class="sub-title">Specialised <span>Treatments</span></h3>
  <ul class="treatments">
    <li class="treatment"><div class="thumb" role="img" aria-label="Photo: diabetic foot check"></div><div class="treatment-body"><h3>Diabetic Management</h3><p>Diabetic Management - Assessment of blood supply / circulation with Doppler Ultrasound; assessment of nerve sensation via Vibration Perception and Monofilament Pressure testing, management and prevention of wounds or ulcers. General foot care and footwear advice for diabetic feet.</p></div></li>
    <li class="treatment"><div class="thumb" role="img" aria-label="Photo: nail surgery"></div><div class="treatment-body"><h3>Nail Surgery</h3><p>Nail Surgery - Minor surgical procedure for the permanent removal of ingrown toenails under local anaesthesia.</p></div></li>
    <li class="treatment"><div class="thumb" role="img" aria-label="Photo: foot being assessed"></div><div class="treatment-body"><h3>Biomechanical Assessment</h3><p>Biomechanical Assessment - We are able to help diagnose abnormal foot biomechanics that may be contributing to pain, injury or deformities in the foot and lower limb.</p></div></li>
    <li class="treatment"><div class="thumb" role="img" aria-label="Photo: runner on a treadmill"></div><div class="treatment-body"><h3>Gait Analysis</h3><p>Gait Analysis - Treadmill video analysis of the gait whilst walking or running to ascertain biomechanical problems or abnormalities of movement that may lead to injury or prevent optimal physical performance.</p></div></li>
    <li class="treatment"><div class="thumb" role="img" aria-label="Photo: orthotic insole"></div><div class="treatment-body"><h3>Orthotic Therapy</h3><p>Orthotic Therapy - Orthose, or arch supports, are designed to control the function of the foot when there is evidence of faulty biomechanics, such as overlay flat or high arched feet or the need to relieve areasor pressure. These may be prefabricated over the counter insoles or custom-made devices.Your podiatrists will assess your foot function and advise which type of device is appropriate for your condition.</p></div></li>
  </ul>
</section>

<section class="partners" aria-label="Partners and accepted providers">
  <div class="badge badge-a"></div>
  <div class="badge badge-b"></div>
  <div class="badge badge-c"></div>
  <div class="badge badge-d"></div>
</section>

<section class="contact">
  <div class="photo-fill" role="img" aria-label="Photo: runner on a country road"></div>
  <h2 class="section-title">Contact us</h2>
  <form class="contact-form">
    <input class="field" placeholder="Name">
    <input class="field" placeholder="E-Mail">
    <input class="field" placeholder="Phone">
    <textarea class="field field-message" placeholder="Message"></textarea>
    <button class="submit" type="button">Submit</button>
  </form>
  <div class="map" role="img" aria-label="Street map of the clinic location"></div>
  <div class="contact-address">
    <h4>Contact address</h4>
    <p><svg width="20" height="26" viewBox="0 0 18 24"><path d="M9 0C4 0 0 4 0 9c0 7 9 15 9 15s9-8 9-15c0-5-4-9-9-9zm0 12a3 3 0 110-6 3 3 0 010 6z" fill="#fff"/></svg><span>Suite 12 / 88 Harrow Lane<br>Ashvale 3100.</span></p>
    <p><svg width="20" height="20" viewBox="0 0 24 24"><path d="M6.6 10.8a15 15 0 006.6 6.6l2.2-2.2c.3-.3.7-.4 1-.2 1.1.4 2.3.6 3.6.6.6 0 1 .4 1 1V20c0 .6-.4 1-1 1A17 17 0 013 4c0-.6.4-1 1-1h3.5c.6 0 1 .4 1 1 0 1.3.2 2.5.6 3.6.1.3 0 .7-.2 1z" fill="#fff"/></svg><strong>1300 555 274</strong></p>
    <p><svg width="20" height="16" viewBox="0 0 20 16"><rect x="1" y="1" width="18" height="14" fill="none" stroke="#fff" stroke-width="2"/><path d="M1 1l9 7 9-7" fill="none" stroke="#fff" stroke-width="2"/></svg>info@brambleridgepodiatry.net</p>
    <a class="social" href="#" aria-label="Social page"></a>
  </div>
</section>

<footer class="site-footer">© Bramble Ridge Podiatry- 2016. All Rights Reserved.</footer>

</body>
</html>
```